Kor'v Meridell Travel

We need a sleek, professional, inviting card to elicit global travel for the experienced and professional traveler. Royal blue, black and silver. (perhaps the wording could be silver with black shadow?-get creative) Maybe a watermark on the front and the full raised logo on the back.
We want a stylish and modern card, but professional.

```html
<!DOCTYPE html>
<html lang="en">
<head>
<meta charset="utf-8">
<title>Kor'v Meridell Travel – Business Card</title>
<link href="https://fonts.googleapis.com/css2?family=Montserrat:wght@400;500;600;700&display=swap" rel="stylesheet">
<style>
  :root {
    --stage: #2b2624;
    --card: #0b0b0b;
    --blue: #27a8e0;
    --green: #8cc63f;
    --white: #ffffff;
    --rule: #6a6a6a;
  }
  * { margin: 0; padding: 0; box-sizing: border-box; }
  html, body { width: 1200px; height: 842px; overflow: hidden; }
  body {
    background: var(--stage);
    font-family: "Montserrat", Arial, sans-serif;
    position: relative;
  }
  .card {
    position: absolute;
    top: 266px;
    width: 540px;
    height: 310px;
    background: var(--card);
    overflow: hidden;
    box-shadow: 0 10px 30px rgba(0,0,0,.45);
  }
  .card--contact { left: 40px; }
  .card--brand { left: 620px; }

  /* contact side */
  .band {
    position: absolute; left: 0; right: 0; height: 11px;
    background: var(--blue);
  }
  .band--top { top: 8px; }
  .band--bottom { bottom: 8px; }

  .contact {
    position: absolute; left: 180px; top: 76px;
    color: var(--white);
    font-size: 12.5px; line-height: 1.5;
    white-space: nowrap;
  }
  .contact__name {
    color: var(--blue); font-weight: 700; font-size: 19px;
    letter-spacing: .2px; text-transform: uppercase; line-height: 1.1;
  }
  .contact__title {
    color: var(--green); font-size: 11px; font-weight: 500;
    text-transform: uppercase; letter-spacing: .3px; padding-left: 16px;
    line-height: 1.3;
  }
  .contact__rule { width: 150px; height: 1px; background: var(--rule); margin: 8px 0 6px 44px; }
  .contact__label { color: var(--blue); font-weight: 700; margin-right: 4px; }
  .contact__lines { padding-left: 40px; }
  .contact__web .accent { color: var(--blue); }
  .contact__address { padding-left: 52px; line-height: 1.4; }

  /* brand side */
  .tab { position: absolute; width: 30px; height: 52px; background: var(--blue); }
  .tab::after {
    content: ""; position: absolute; top: 0; width: 4px; height: 100%;
    background: var(--green);
  }
  .tab--left { left: 0; top: 122px; }
  .tab--left::after { right: -6px; }
  .tab--right { right: 0; top: 0; }
  .tab--right::after { left: -6px; }

  .brand {
    position: absolute; left: 0; right: 0; top: 0; bottom: 0;
    display: flex; align-items: center; justify-content: center; gap: 12px;
  }
  .brand__mark { width: 16px; height: 16px; background: var(--green); }
  .brand__name {
    color: var(--blue); font-weight: 600; font-size: 24px;
    letter-spacing: 1.2px; text-transform: uppercase;
  }
</style>
</head>
<body>
  <section class="card card--contact">
    <div class="band band--top"></div>
    <div class="contact">
      <div class="contact__name">Edric Valmont</div>
      <div class="contact__title">Managing Director</div>
      <div class="contact__rule"></div>
      <div class="contact__lines">
        <div><span class="contact__label">P:</span>044-318 207 645</div>
        <div><span class="contact__label">M:</span>044-318 207 690</div>
        <div><span class="contact__label">E:</span>info@korvmeridell.com</div>
        <div class="contact__web">www.<span class="accent">korvmeridell</span>.com</div>
      </div>
      <div class="contact__rule"></div>
      <div class="contact__address">
        <div>87, Harbour Lane, Suite 4</div>
        <div>60318, Calveria</div>
      </div>
    </div>
    <div class="band band--bottom"></div>
  </section>

  <section class="card card--brand">
    <div class="tab tab--left"></div>
    <div class="tab tab--right"></div>
    <div class="brand">
      <span class="brand__mark"></span>
      <span class="brand__name">Kor'v Meridell Travel</span>
    </div>
  </section>
</body>
</html>
```